RESIDENTIAL CONSTRUCTION

We are a company that specializes in building custom residential homes, the design should also emphasize that quality and service is our priority.

Industry/Entity Type

Construction Company

Contact Information for Business Card

Contact Person: Marcus Lindqvist
Company Address: 273 West Alder Ave San Jose , Ca 95380
Phone Number : 408-731-2946
Email Address: Stoneridgehomes517@mailvista.net

Font styles to use
Sans Serif

Colors
ec1f27

Requirements
Must have
• CSLB # 7362015
Nice to have
• needs to have same color as logo i uploaded, we will be printing these on a clear plastic card.

```html
<!DOCTYPE html>
<html lang="en">
<head>
<meta charset="utf-8">
<title>Stoneridge Homes – Business Card</title>
<link rel="stylesheet" href="https://fonts.googleapis.com/css2?family=Roboto:wght@400&family=Roboto+Condensed:wght@700&display=swap">
<style>
  :root {
    --backdrop: #1b1b1b;
    --card: #f4f4f4;
    --edge-band: #dcdcdc;
    --brand-red: #ec1f27;
    --ink: #111111;
    --text-grey: #5f5f5f;
  }
  * { margin: 0; padding: 0; box-sizing: border-box; }
  html, body { width: 1200px; height: 826px; overflow: hidden; background: var(--backdrop); }
  .canvas { position: relative; width: 1200px; height: 826px; }
  .card {
    position: absolute; left: 390px; top: 45px; width: 420px; height: 736px;
    background: var(--card);
  }
  .edge-band {
    position: absolute; inset: 0;
    border: 22px solid var(--edge-band);
  }
  .card-content {
    position: absolute; left: 0; right: 0; top: 218px;
    display: flex; flex-direction: column; align-items: center; text-align: center;
  }
  .brand { display: flex; align-items: center; gap: 9px; }
  .brand-square { width: 26px; height: 26px; background: var(--brand-red); }
  .brand-name {
    font-family: "Roboto Condensed", sans-serif; font-weight: 700;
    font-size: 32px; color: var(--ink); letter-spacing: 0.5px; text-transform: uppercase;
  }
  .person-name {
    margin-top: 26px;
    font-family: "Roboto Condensed", sans-serif; font-weight: 700;
    font-size: 27px; color: var(--brand-red); letter-spacing: 0.3px;
  }
  .icon-row { margin-top: 22px; display: flex; align-items: center; gap: 9px; }
  .icon-rule { width: 42px; height: 2px; background: var(--ink); margin: 0 4px; }
  .icon-box { width: 28px; height: 25px; background: var(--ink); display: flex; align-items: center; justify-content: center; }
  .icon-box svg { width: 15px; height: 15px; }
  .contact {
    font-family: "Roboto", sans-serif; font-weight: 400; color: var(--text-grey);
    font-size: 18.5px; line-height: 24px;
  }
  .contact.address { margin-top: 20px; }
  .contact.lines { margin-top: 14px; }
  .contact.license { margin-top: 16px; }
</style>
</head>
<body>
<div class="canvas">
  <div class="card">
    <div class="edge-band" role="img" aria-label="Measuring-ruler tick border along the card edges"></div>

    <div class="card-content">
      <div class="brand">
        <span class="brand-square"></span>
        <span class="brand-name">Stoneridge Homes</span>
      </div>
      <div class="person-name">MARCUS LINDQVIST</div>

      <div class="icon-row">
        <span class="icon-rule"></span>
        <span class="icon-box" aria-label="Address">
          <svg viewBox="0 0 16 16"><path d="M8 1a5 5 0 0 0-5 5c0 3.6 5 9 5 9s5-5.4 5-9a5 5 0 0 0-5-5zm0 7a2 2 0 1 1 0-4 2 2 0 0 1 0 4z" fill="#ec1f27"/></svg>
        </span>
        <span class="icon-box" aria-label="Phone">
          <svg viewBox="0 0 16 16"><path d="M4 1.5l2.2 2.8-1.3 1.8c.9 2 2.5 3.6 4.5 4.5l1.8-1.3 2.8 2.2-1.2 2.3C7.6 13.6 2.4 8.4 1.7 2.7z" fill="#ec1f27"/></svg>
        </span>
        <span class="icon-box" aria-label="Email">
          <svg viewBox="0 0 16 16"><rect x="2" y="4" width="12" height="8" fill="#ec1f27"/><path d="M2 4l6 5 6-5" fill="none" stroke="#111" stroke-width="1.2"/></svg>
        </span>
        <span class="icon-box" aria-label="Website">
          <svg viewBox="0 0 16 16"><circle cx="8" cy="8" r="6" fill="#ec1f27"/><path d="M2 8h12M8 2c-2.5 3-2.5 9 0 12M8 2c2.5 3 2.5 9 0 12" fill="none" stroke="#111" stroke-width="1"/></svg>
        </span>
        <span class="icon-rule"></span>
      </div>

      <p class="contact address">273 West Alder Ave San<br>Jose, Ca 95380</p>
      <p class="contact lines">408-731-2946<br>Stoneridgehomes517@mailvista.net<br>www.stoneridgehomes.net</p>
      <p class="contact license">CSLB # 7362015</p>
    </div>
  </div>
</div>
</body>
</html>
```